NCBG website design

We need a page template website design for a cms website. Please see the brief attached for the details.
The client is the National Copperfleece Breeders Guild which is an organisation promoting the Copperfleece Sheep Breed within Australia.
Updates

Project Deadline Extended
Reason: So that my top few designs can make changes and re-submit.

Target Market(s)

See attached brief

```html
<!DOCTYPE html>
<html lang="en">
<head>
<meta charset="utf-8">
<title>National Copperfleece Breeders Guild</title>
<link href="https://fonts.googleapis.com/css2?family=Lato:wght@300;400;700&display=swap" rel="stylesheet">
<style>
:root{
  --green:#0e8a3e;
  --nav-green:#0b6b2c;
  --nav-dark:#2b2b2b;
  --ink:#2a2a2a;
  --page-bg:#efefef;
  --footer-bg:#231f20;
  --footer-text:#d6d6d6;
  --label-yellow:#f2e600;
  --sponsor-red:#e04a2a;
}
*{box-sizing:border-box;margin:0;padding:0}
html,body{width:1120px;height:1200px;overflow:hidden}
body{background:var(--page-bg);font-family:'Lato',sans-serif;color:var(--ink);position:relative}
.header-band{position:absolute;left:0;top:0;width:1120px;height:143px;background:#fff;box-shadow:0 2px 4px rgba(0,0,0,.15)}
.wrap{position:absolute;left:170px;top:0;width:781px;height:1060px;background:#fff;box-shadow:0 0 4px rgba(0,0,0,.18)}
.brand{position:absolute;left:8px;top:36px;display:flex;align-items:center;gap:8px}
.brand-mark{width:20px;height:20px;border-radius:50%;background:var(--green)}
.brand-name{font-weight:700;font-size:22px;color:var(--green)}
.site-title{position:absolute;left:202px;top:36px;font-weight:700;font-size:28px;letter-spacing:-.2px;color:#222;white-space:nowrap}
.main-nav{position:absolute;left:0;top:101px;width:781px;height:42px;display:flex;background:var(--nav-green)}
.main-nav a{color:#fff;text-decoration:none;font-weight:700;font-size:13px;display:flex;align-items:center;justify-content:center;border-right:1px solid #075823;height:100%}
.main-nav a.active{background:var(--nav-dark)}
.hero{position:absolute;left:0;top:143px;width:781px;height:176px;background:linear-gradient(180deg,#6f6a55 0%,#b79a6c 45%,#c8a67a 75%,#8a4a2a 100%)}
.promo{position:absolute;left:25px;width:227px;height:95px;border:1px solid #222;overflow:hidden}
.promo-photo{position:absolute;inset:0}
.promo-band{position:absolute;left:0;bottom:0;width:100%;height:44px;background:rgba(30,30,30,.88);display:flex;align-items:center;padding-left:7px}
.promo-label{color:var(--label-yellow);font-weight:700;font-size:12.5px}
.promo-links{margin-left:auto;margin-right:12px;display:flex;flex-direction:column;gap:6px;color:#fff;font-weight:700;font-size:10.5px}
.sponsors{position:absolute;left:27px;top:804px;width:224px}
.sponsors h3{font-size:15px;font-weight:700;color:#111;margin-bottom:3px}
.ad{width:224px;height:175px;background:linear-gradient(180deg,var(--sponsor-red) 0%,var(--sponsor-red) 26%,#8a7a5a 32%,#7a4a2a 60%,#6f7a45 86%,var(--sponsor-red) 88%)}
.view-all{display:block;margin-top:8px;margin-left:1px;color:var(--green);font-weight:700;font-size:11.5px;text-decoration:none}
.content{position:absolute;left:277px;top:341px;width:474px;font-size:12.9px;line-height:20.8px}
.welcome{font-weight:300;font-size:29px;line-height:32px;color:#222}
.content h1{font-weight:700;font-size:29px;line-height:34px;color:var(--green);margin-bottom:8px;white-space:nowrap}
.content h2{font-weight:400;font-size:15px;color:var(--green);margin:19px 0 2px}
.content strong{font-weight:700;color:#111}
.content a{color:var(--green)}
.ticks{list-style:none;line-height:23.2px}
.ticks li{display:flex;align-items:center;gap:5px}
.footer{position:absolute;left:0;top:1060px;width:1120px;height:140px;background:var(--footer-bg);border-top:6px solid #3b3b3b;color:var(--footer-text);font-size:11.5px}
.copy{position:absolute;left:170px;top:29px;line-height:21px}
.copy a{color:var(--green);text-decoration:none}
.follow{position:absolute;left:494px;top:26px;display:flex;align-items:center;gap:10px}
.social-square{width:21px;height:21px;background:#3b5998;border-radius:2px}
.contact{position:absolute;left:698px;top:24px;border-collapse:collapse}
.contact td{padding:0;height:20.8px;line-height:20.8px}
.contact td:nth-child(2){width:38px;text-align:center}
.contact td:first-child{width:56px}
</style>
</head>
<body>
<div class="header-band"></div>
<div class="wrap">
  <header>
    <div class="brand"><span class="brand-mark"></span><span class="brand-name">Copperfleece</span></div>
    <div class="site-title">NATIONAL COPPERFLEECE BREEDERS GUILD</div>
  </header>
  <nav class="main-nav">
    <a class="active" href="#" style="width:73px">HOME</a>
    <a href="#" style="width:76px">ABOUT</a>
    <a href="#" style="width:83px">SEARCH</a>
    <a href="#" style="width:148px">MEMBER SERVICES</a>
    <a href="#" style="width:108px">STUD PAGES</a>
    <a href="#" style="width:70px">NEWS</a>
    <a href="#" style="width:66px">SALES</a>
    <a href="#" style="width:68px">LINKS</a>
    <a href="#" style="width:89px;border-right:0">CONTACT</a>
  </nav>
  <div class="hero" role="img" aria-label="A row of copperfleece sheep standing on red earth before a hillside"></div>

  <aside>
    <div class="promo" style="top:345px">
      <div class="promo-photo" role="img" aria-label="Helpline operator with a headset beside a lamb in a green paddock" style="background:linear-gradient(90deg,#c9a58a,#7a9a4a 55%,#9bb860)"></div>
      <div class="promo-band"><span class="promo-label">PRIME LAMB HELPLINE</span></div>
    </div>
    <div class="promo" style="top:458px">
      <div class="promo-photo" role="img" aria-label="Close-up of a calendar page with a date circled in red" style="background:linear-gradient(180deg,#f4f4f4,#dcdcdc)"></div>
      <div class="promo-band"><span class="promo-label">EVENTS</span></div>
    </div>
    <div class="promo" style="top:570px">
      <div class="promo-photo" role="img" aria-label="Two people shaking hands" style="background:linear-gradient(90deg,#2a2a2a,#d8b49a 50%,#3a3a6a)"></div>
      <div class="promo-band"><span class="promo-label">MEMBERS</span>
        <div class="promo-links"><span>MEMBERS RESOURCES</span><span>WEBMANAGER LOGIN</span></div>
      </div>
    </div>
    <div class="promo" style="top:683px">
      <div class="promo-photo" role="img" aria-label="Reading glasses on a newspaper beside a coffee cup" style="background:linear-gradient(180deg,#f5f5f5,#cfcfcf)"></div>
      <div class="promo-band"><span class="promo-label">LATEST NEWS</span></div>
    </div>
    <div class="sponsors">
      <h3>SPONSORS</h3>
      <div class="ad" role="img" aria-label="Sponsor advertisement banner for a livestock trading partner"></div>
      <a class="view-all" href="#">VIEW ALL SPONSORS&gt;</a>
    </div>
  </aside>

  <main class="content">
    <div class="welcome">WELCOME TO</div>
    <h1>National Copperfleece Breeders Guild</h1>
    <p>Lorem ipsum dolor sit amet, consectetur adipiscing elit. Sed quis nisi euismod, fermentum tellus a, lobortis quam. <strong>Vestibulum condimentum</strong> mi vitae diam tristique, egestas dignissim diam mattis. <a href="#">Curabitur vel diam</a> in massa porttitor dictum id in lorem.</p>
    <h2>Vivamus faucibus ac leo ac dignissim.</h2>
    <p>Maecenas orci est, euismod facilisis feugiat sit amet, semper ut tortor. Donec eleifend accumsan nisl, nec laoreet leo iaculis sit amet. Vivamus varius arcu eu sagittis aliquam. Vivamus accumsan cursus hendrerit. <strong>Vivamus eu magna rhoncus</strong>, consectetur metus ac, varius lacus.</p>
    <h2>Donec ultricies, tortor quis sagittis sagittis</h2>
    <ul class="ticks">
      <li><svg width="11" height="9" viewBox="0 0 11 9"><path d="M1 4.5l3 3 6-6" fill="none" stroke="#0e8a3e" stroke-width="2.2"/></svg>Mauris erat ullamcorper augue, eu placerat diam nunc a lorem.</li>
      <li><svg width="11" height="9" viewBox="0 0 11 9"><path d="M1 4.5l3 3 6-6" fill="none" stroke="#0e8a3e" stroke-width="2.2"/></svg>Nam vulputate mauris id arcu pharetra, sed posuere quam cursus.</li>
      <li><svg width="11" height="9" viewBox="0 0 11 9"><path d="M1 4.5l3 3 6-6" fill="none" stroke="#0e8a3e" stroke-width="2.2"/></svg>Nullam eget massa vel mi posuere venenatis sed quis tortor.</li>
      <li><svg width="11" height="9" viewBox="0 0 11 9"><path d="M1 4.5l3 3 6-6" fill="none" stroke="#0e8a3e" stroke-width="2.2"/></svg>In hac habitasse platea dictumst. Fusce nisi tellus, fermentum.</li>
      <li><svg width="11" height="9" viewBox="0 0 11 9"><path d="M1 4.5l3 3 6-6" fill="none" stroke="#0e8a3e" stroke-width="2.2"/></svg>In commodo egestas magna quis placerat. Quisque adipiscing consequat nisi.</li>
    </ul>
    <h2>Cras accumsan orci mauris ut aliquam ipsum faucibus sed.</h2>
    <p>Fusce quam dui, accumsan a magna in, faucibus tristique lectus. Vestibulum sapien leo, placerat quis luctus eget, auctor et justo. Vestibulum ante ipsum primis in faucibus orci luctus et ultrices posuere cubilia Curae; <strong>Duis sagittis</strong>, risus ut viverra dignissim, lectus nunc iaculis arcu, et gravida est tortor ut erat. Morbi a feugiat dolor, in tristique elit. Mauris feugiat aliquam vulputate.</p>
    <h2>Vivamus faucibus ac leo ac dignissim.</h2>
    <p>Vivamus varius arcu eu sagittis aliquam. Vivamus accumsan cursus hendrerit. Vivamus eu magna rhoncus, consectetur metus ac, varius lacus.</p>
  </main>
</div>

<footer class="footer">
  <div class="copy">Copyright National Copperfleece Breeders Guild<br><a href="#">Website design and development by Ridgeway Web</a></div>
  <div class="follow"><span>Follow us on:</span><span class="social-square"></span></div>
  <table class="contact">
    <tr><td>Address</td><td>:</td><td>PO Box 412, Kenton, SA 5071</td></tr>
    <tr><td>Phone</td><td>:</td><td>08 8100 4417</td></tr>
    <tr><td>Fax</td><td>:</td><td>08 8100 4418</td></tr>
    <tr><td>Email</td><td>:</td><td>guild@copperfleece.org.au</td></tr>
  </table>
</footer>
</body>
</html>
```